Simplified minimalist but bold website

Design a website for a brand 'Brighten Every Day' that shares ideas to make managing home and health easier through email swap series, webinars and eventually courses.

Simple landing page to attract users to sign up for a freebie.

Target Market(s)

women with families & homes to run

Number of Pages Required

1 page

Font styles to use
Sans Serif

Colors
e667a6
b768aa
acd136
ffffff
959595

Requirements
Must have
• Simplified look, line icons, opt-in template, contact us form

```html
<!DOCTYPE html>
<html lang="en">
<head>
<meta charset="utf-8">
<title>Brighten Every Day</title>
<link rel="stylesheet" href="https://fonts.googleapis.com/css2?family=Quicksand:wght@400;500;600;700&family=Poppins:wght@400;500;600&display=swap">
<style>
:root{
  --pink:#e667a6;
  --purple:#b768aa;
  --green:#acd136;
  --grey:#959595;
  --white:#ffffff;
  --ink:#1f1f1f;
  --muted:#3a3a3a;
  --footer:#1b1e22;
  --footer-text:#d8d8d8;
}
*{box-sizing:border-box;margin:0;padding:0}
html,body{width:1200px;height:2177px;overflow:hidden}
body{position:relative;font-family:"Poppins",sans-serif;color:var(--ink);background:var(--white)}
.abs{position:absolute}
.center{text-align:center}

/* hero */
.hero{left:0;top:0;width:1200px;height:523px;overflow:hidden}
.hero-photo{position:absolute;inset:0;background:
  linear-gradient(90deg,#e9e6e3 0%,#dcd6d0 25%,#c9c0b8 45%,#b9a9a4 60%,#c87a6a 68%,#e6e1dc 80%,#f2efec 100%)}
.hero-shade{position:absolute;inset:0;background:rgba(40,40,40,.18)}
.brand{left:113px;top:30px;font-family:"Quicksand",sans-serif;font-weight:700;font-size:38px;color:var(--pink);display:flex;align-items:center;gap:10px}
.brand-dot{width:22px;height:22px;border-radius:50%;background:var(--green)}
.menu{left:1073px;top:38px;width:18px}
.menu span{display:block;height:3px;background:#222;margin-bottom:3px}
.hero-title{left:0;width:1200px;top:190px;font-family:"Quicksand",sans-serif;font-weight:500;font-size:48px;letter-spacing:6px;color:var(--white)}
.hero-sub{left:0;width:1200px;top:274px;font-family:"Quicksand",sans-serif;font-size:21px;color:var(--white)}
.btn{display:flex;align-items:center;justify-content:center;font-family:"Poppins",sans-serif;font-weight:600;font-size:14px;letter-spacing:.5px;border-radius:3px;text-transform:uppercase}
.btn-pink{background:var(--pink);color:var(--white)}
.btn-purple{background:var(--purple);color:var(--white)}
.btn-outline{border:2px solid var(--pink);color:var(--pink);background:var(--white)}
.hero-btn{left:513px;top:317px;width:174px;height:40px}
.scroll-down{left:583px;top:456px}

/* offers */
.kicker{font-size:14.5px;color:var(--muted)}
.offer-title{font-family:"Quicksand",sans-serif;font-weight:600;font-size:22px;color:var(--purple)}
.rule{height:3px;width:40px;background:var(--green)}
.copy{font-size:13px;line-height:30px;color:var(--muted)}
.feature{width:120px;text-align:center}
.feature-label{font-family:"Quicksand",sans-serif;font-weight:700;font-size:15px;margin-top:6px;color:var(--ink)}
.feature-link{font-size:12.5px;color:var(--pink);text-decoration:underline;line-height:22px;margin-top:6px}

/* opt-in forms */
.optin{width:461px;height:288px;padding:40px 53px 0}
.optin-green{background:var(--green)}
.optin-purple{background:var(--purple);box-shadow:0 4px 14px rgba(0,0,0,.15)}
.optin h3{font-family:"Quicksand",sans-serif;font-weight:500;font-size:17px;color:var(--white);text-align:center;margin-bottom:24px}
.field{height:44px;background:var(--white);border:1px solid #ddd;padding:0 14px;display:flex;align-items:center;font-size:13px;color:#666;margin-bottom:13px}
.optin .btn{height:44px;font-size:15px}
.btn-ghost{border:2px solid var(--white);color:var(--white)}

/* series band */
.band{left:0;top:1338px;width:1200px;height:492px;overflow:hidden}
.band-photo{position:absolute;inset:0;background:linear-gradient(90deg,#e9d3d3 0%,#f0e2e0 30%,#efe6e6 55%,#f3e1e4 80%,#efe9e9 100%)}
.band-veil{position:absolute;inset:0;background:rgba(255,255,255,.55)}
.band-title{font-family:"Quicksand",sans-serif;font-weight:500;font-size:30px;color:var(--ink)}
.band-line{font-size:13.5px;line-height:30px;color:var(--ink)}
.band-strong{font-weight:600;font-size:16px}

/* footer */
.footer{left:0;top:1830px;width:1200px;height:347px;background:var(--footer);color:var(--footer-text)}
.contact{display:flex;gap:20px;align-items:flex-start;font-size:14.5px;line-height:24px}
.contact-ring{width:44px;height:44px;border:2px solid var(--footer-text);border-radius:50%;display:flex;align-items:center;justify-content:center;flex:none}
.contact-form{display:flex;gap:14px}
.contact-field{height:40px;border:1px solid #4a4f56;background:#24282d;color:var(--grey);font-size:13px;padding:0 14px;display:flex;align-items:center}
.contact-form .btn{height:40px;width:150px;font-size:13px}
.socials{display:flex;gap:24px}
.social-dot{width:24px;height:24px;border-radius:4px;background:#e6e6e6}
.foot-nav{font-size:15.5px;color:#e6e6e6}
.foot-nav span{margin:0 8px}
.copyright{font-size:12px;color:#cfcfcf}
</style>
</head>
<body>

<section class="abs hero">
  <div class="hero-photo" role="img" aria-label="Photo of a woman sorting clothes in a bright wardrobe"></div>
  <div class="hero-shade"></div>
  <div class="abs brand"><span class="brand-dot"></span>Brighten</div>
  <div class="abs menu"><span></span><span></span><span></span></div>
  <h1 class="abs hero-title center">BRIGHTEN EVERY DAY.</h1>
  <p class="abs hero-sub center">Chances are life is a little overwhelming.</p>
  <a class="abs btn btn-pink hero-btn">Let us help</a>
  <svg class="abs scroll-down" width="34" height="34" viewBox="0 0 34 34" aria-hidden="true">
    <circle cx="17" cy="17" r="15" fill="none" stroke="#fff" stroke-width="2.5"/>
    <path d="M10 14l7 7 7-7" fill="none" stroke="#fff" stroke-width="2.5"/>
  </svg>
</section>

<!-- left offer -->
<p class="abs kicker center" style="left:114px;width:461px;top:618px">Baby Steps... (try out a few of our tricks)</p>
<h2 class="abs offer-title center" style="left:114px;width:461px;top:655px">Swaps Email Series</h2>
<div class="abs rule" style="left:324px;top:700px"></div>
<p class="abs copy center" style="left:114px;width:461px;top:719px;font-size:14px">Save TIME, MONEY and SANITY with simple product swaps.</p>
<p class="abs copy center" style="left:170px;width:350px;top:758px">Reduce the amount of work it takes to run your home.Swap out existing products for more sustainable ones.Each swap saves you work, clutter, time &amp; money.</p>
<a class="abs btn btn-outline" style="left:195px;top:874px;width:164px;height:39px;font-size:13px">See sample swap</a>
<a class="abs btn btn-pink" style="left:374px;top:874px;width:122px;height:39px;font-size:13px">Learn more</a>

<!-- right offer -->
<p class="abs kicker center" style="left:627px;width:461px;top:618px">Big Leap... (I'm ready to roll up my sleeves)</p>
<h2 class="abs offer-title center" style="left:627px;width:461px;top:655px">Decluttering Guide</h2>
<div class="abs rule" style="left:838px;top:700px"></div>
<div class="abs feature" style="left:719px;top:758px">
  <svg width="44" height="44" viewBox="0 0 44 44" aria-hidden="true" fill="none" stroke="#e667a6" stroke-width="2">
    <rect x="6" y="3" width="26" height="34" rx="2"/>
    <path d="M11 11l2 2 3-3M19 12h8M11 19l2 2 3-3M19 20h8M11 27h16"/>
    <circle cx="33" cy="33" r="7" fill="#fff"/><path d="M30 33l2 2 4-4"/>
  </svg>
  <div class="feature-label">Steps</div>
  <div class="feature-link">Let Us Help</div>
</div>
<div class="abs feature" style="left:882px;top:758px">
  <svg width="44" height="44" viewBox="0 0 44 44" aria-hidden="true" fill="none" stroke="#e667a6" stroke-width="2" stroke-linejoin="round">
    <rect x="6" y="19" width="8" height="19"/>
    <path d="M14 21l7-10c1-3 5-3 5 1l-2 8h10c3 0 4 3 3 5l-3 10c-1 2-2 3-4 3H14"/>
  </svg>
  <div class="feature-label">Simple</div>
  <div class="feature-link">Chances Let<br>Us Help</div>
</div>

<!-- opt-in forms -->
<form class="abs optin optin-green" style="left:114px;top:952px">
  <h3>Send your ideas my way...</h3>
  <div class="field">Name</div>
  <div class="field">Email</div>
  <div class="btn btn-pink">Send me the guide</div>
</form>
<form class="abs optin optin-purple" style="left:627px;top:953px">
  <h3>Send your ideas my way...</h3>
  <div class="field">Name</div>
  <div class="field">Email</div>
  <div class="btn btn-ghost">Sign me up</div>
</form>

<!-- series band -->
<section class="abs band">
  <div class="band-photo" role="img" aria-label="Soft faded photo of colourful clothes on a rail"></div>
  <div class="band-veil"></div>
  <h2 class="abs band-title center" style="left:0;width:1200px;top:87px">Swaps Email Series</h2>
  <div class="abs rule" style="left:580px;top:141px"></div>
  <div class="abs center" style="left:0;width:1200px;top:174px">
    <p class="band-line">Save TIME, MONEY and SANITY with simple product swaps.And reduce the amount of work it takes to run your home.</p>
    <p class="band-line">Swap out existing products for more sustainable ones.Each swap save you work, clutter, time &amp; money.</p>
    <p class="band-line band-strong" style="line-height:34px">You get an email 2x weekly for 6-12 weeks only Get even more if you feel they are helpful to you</p>
    <p class="band-line" style="font-weight:500">Join our monthly SIMPLE SWAP SHARING web jams with other mums and get even more ideas.</p>
    <p class="band-line" style="font-weight:500">Better yet, come with great tips of your own to share.</p>
  </div>
  <a class="abs btn btn-pink" style="left:494px;top:357px;width:213px;height:38px;font-size:15px">Sign me up!</a>
</section>

<!-- footer -->
<footer class="abs footer">
  <div class="abs contact" style="left:113px;top:50px">
    <div class="contact-ring"><svg width="18" height="22" viewBox="0 0 18 22" aria-hidden="true"><path d="M9 1a7 7 0 0 0-7 7c0 5 7 13 7 13s7-8 7-13a7 7 0 0 0-7-7z" fill="#d8d8d8"/><circle cx="9" cy="8" r="2.5" fill="#1b1e22"/></svg></div>
    <div>Brighten Every Day,Clara Wendt<br>Lindenhof 14 ,80469 Munich</div>
  </div>
  <div class="abs contact" style="left:546px;top:50px">
    <div class="contact-ring"><svg width="20" height="20" viewBox="0 0 20 20" aria-hidden="true"><path d="M4 1l4 4-2 3c1 2 4 5 6 6l3-2 4 4-3 3C9 19 1 11 1 4z" fill="#d8d8d8"/></svg></div>
    <div>Phone :<br>+(01) 555 010 2040</div>
  </div>
  <div class="abs contact" style="left:881px;top:50px">
    <div class="contact-ring"><svg width="20" height="16" viewBox="0 0 20 16" aria-hidden="true" fill="none" stroke="#d8d8d8" stroke-width="2"><rect x="1" y="1" width="18" height="14" rx="2"/><path d="M1 3l9 6 9-6"/></svg></div>
    <div>E - Mail :<br>hello@brighten.example</div>
  </div>

  <form class="abs contact-form" style="left:113px;top:138px">
    <div class="contact-field" style="width:220px">Name</div>
    <div class="contact-field" style="width:240px">Email</div>
    <div class="contact-field" style="width:326px">Message</div>
    <div class="btn btn-pink">Contact us</div>
  </form>

  <div class="abs socials" style="left:492px;top:216px">
    <span class="social-dot"></span><span class="social-dot"></span><span class="social-dot"></span><span class="social-dot"></span><span class="social-dot"></span>
  </div>
  <nav class="abs foot-nav center" style="left:0;width:1200px;top:284px">Home<span>|</span>About us<span>|</span>Gallery<span>|</span>Services<span>|</span>Contact us</nav>
  <p class="abs copyright center" style="left:0;width:1200px;top:321px">Copyright © 2018 Brighten Every Day. All Rights Reserved. Privacy Policy | Terms Of Use</p>
</footer>

</body>
</html>
```